Build Distinctive Business Card: Public Relations Government Relations firm

I have logo and colors done (attached) need a very cool way to present it on a business card (can be two sided if need be).

Public Relations Government Relations firm

Info:

Paul Marchetti, CEO
Keystone Public Relations
2730 West Harlan Blvd.
Los Angeles CA 90012
(o) 213.555.0148
(f) 213.555.0173
paul@keystonekpr-example.com

Target Market(s)

Government relations, public relations, lobbyist, I was a past State Senator

Industry/Entity Type

Business

Contact Information for Business Card

Info:

Paul Marchetti, CEO
Keystone Public Relations
2730 West Harlan Blvd.
Los Angeles CA 90012
(o) 213.555.0148
(f) 213.555.0173
paul@keystonekpr-example.com
@paulmarchetti

Requirements
Must have
• A sense of balance given logo is already done.
• It's a government relations firm really.
• Lobbyist type.
• Senatorial type...

```html
<!DOCTYPE html>
<html lang="en">
<head>
<meta charset="utf-8">
<title>Keystone Public Relations – Business Card</title>
<link rel="stylesheet" href="https://fonts.googleapis.com/css2?family=Arimo:wght@400;700&display=swap">
<style>
  :root {
    --stage: #013260;
    --card-dark: #000000;
    --card-light: #ffffff;
    --brand-blue: #0b5cb2;
    --ink: #111111;
    --shadow: rgba(0, 0, 0, 0.55);
  }
  html, body {
    margin: 0;
    padding: 0;
    width: 1200px;
    height: 1000px;
    overflow: hidden;
    background: var(--stage);
    font-family: "Arimo", Arial, sans-serif;
  }
  .canvas {
    position: relative;
    width: 1200px;
    height: 1000px;
  }
  .card {
    position: absolute;
    left: 293px;
    width: 613px;
    height: 360px;
    box-shadow: -6px 6px 8px var(--shadow);
  }
  .card--front { top: 123px; background: var(--card-dark); }
  .card--back  { top: 517px; height: 359px; background: var(--card-light); }

  .brand-dot {
    position: absolute;
    border-radius: 50%;
    background: var(--brand-blue);
  }
  .brand-name {
    position: absolute;
    margin: 0;
    color: var(--brand-blue);
    font-weight: 700;
    white-space: nowrap;
    line-height: 1;
  }
  .brand-name__line { display: block; }

  .card--front .brand-dot { left: 123px; top: 113px; width: 132px; height: 132px; }
  .card--front .brand-name { left: 267px; top: 150px; }
  .card--front .brand-name__main { font-size: 52px; }
  .card--front .brand-name__sub { font-size: 13px; letter-spacing: 2.4px; margin-top: 6px; padding-left: 32px; }

  .card--back .brand-dot { left: 35px; top: 28px; width: 110px; height: 110px; }
  .card--back .brand-name { left: 155px; top: 56px; }
  .card--back .brand-name__main { font-size: 44px; }
  .card--back .brand-name__sub { font-size: 11px; letter-spacing: 1.8px; margin-top: 4px; padding-left: 27px; }

  .contact {
    position: absolute;
    right: 21px;
    color: var(--ink);
    text-align: right;
    white-space: nowrap;
  }
  .person { top: 135px; }
  .person__name { margin: 0; font-size: 19px; font-weight: 400; line-height: 24px; }
  .person__name strong { font-weight: 700; }
  .person__title { margin: 0; font-size: 14px; line-height: 18px; }

  .details { top: 243px; font-size: 15px; line-height: 20px; }
  .details p { margin: 0; }
  .details .label { margin-right: 8px; }
  .details .email { margin-top: 5px; }
  .details .address { margin-top: 15px; }
</style>
</head>
<body>
<main class="canvas">
  <section class="card card--front" aria-label="Card front">
    <span class="brand-dot" aria-hidden="true"></span>
    <h1 class="brand-name">
      <span class="brand-name__line brand-name__main">Keystone</span>
      <span class="brand-name__line brand-name__sub">PUBLIC RELATIONS</span>
    </h1>
  </section>

  <section class="card card--back" aria-label="Card back">
    <span class="brand-dot" aria-hidden="true"></span>
    <h2 class="brand-name">
      <span class="brand-name__line brand-name__main">Keystone</span>
      <span class="brand-name__line brand-name__sub">PUBLIC RELATIONS</span>
    </h2>

    <div class="contact person">
      <p class="person__name">Paul <strong>Marchetti</strong></p>
      <p class="person__title">CEO</p>
    </div>

    <div class="contact details">
      <p><span class="label">T:</span>213.555.0148</p>
      <p><span class="label">F:</span>213.555.0173</p>
      <p class="email"><span class="label">E:</span>paul@keystonekpr-example.com</p>
      <p class="address">2730 West Harlan Blvd., Los Angeles CA 90012</p>
    </div>
  </section>
</main>
</body>
</html>
```